Business Card Design Project

Looking for a logo and business card for a Real State Business i will be opening. The name is not choosen yet , but will probably be RWT IMOVEIS.
I was thinking black and silver colors, but am open to nice ideas.
I did add a business card that i liked a lot, am looking for something like that, with logo in black or silver in a black card. The logo i was thinking in the letters RWT as i uploaded or something or little and cute buildings or a house...just ideas, can be any nice logo.
Updates

You guys can add other colors if you want, I like colors very "BRIGHT" and "open", like red, pink, strong colors. almost glow in the dark colors. lol

Designers,

I've increased more 88 dollars in the budget for 1st place cause I will want envelope designs... small and big sizes.

So 1st place is now U$248,00. 

No need to send the envelope designs right now... only the business cards designs.

Thank you.

Industry/Entity Type

Business

Requirements
Must have
• Marcela Tavares Rocha

www.RWTimoveis-exemplo.com.br

+554187316042

marcela@rwtimoveis-exemplo.com.br

```html
<!DOCTYPE html>
<html lang="pt-BR">
<head>
<meta charset="utf-8">
<title>RWT Imoveis – Cartões de visita</title>
<link href="https://fonts.googleapis.com/css2?family=Arimo:wght@400;700&family=Ultra&family=Source+Sans+3:wght@400&display=swap" rel="stylesheet">
<style>
  :root {
    --sheet: #ffffff;
    --card: #0b0906;
    --card-shade: #000000;
    --pink: #e2075f;
    --white: #ffffff;
    --label: #111111;
  }
  * { margin: 0; padding: 0; box-sizing: border-box; }
  html, body { width: 1000px; height: 1200px; overflow: hidden; background: var(--sheet); }
  .sheet { position: relative; width: 1000px; height: 1200px; }
  .option-label {
    position: absolute; left: 95px; top: 44px;
    font: 400 52px/1 "Source Sans 3", sans-serif; color: var(--label);
  }
  .card {
    position: absolute; left: 238px; width: 613px; height: 354px;
    background: var(--card); overflow: hidden;
  }
  .card--front { top: 44px; }
  .card--back-pink { top: 423px; }
  .card--back-white { top: 802px; }
  .backdrop-name {
    position: absolute; right: -20px; top: 30px;
    font: 700 190px/1 "Arimo", sans-serif; color: var(--card-shade);
    letter-spacing: 4px;
  }
  .brand-name { position: absolute; font-family: "Arimo", sans-serif; font-weight: 700; line-height: 1; }
  .card--front .brand-name { left: 92px; top: 158px; font-size: 38px; color: var(--pink); }
  .card--back-pink .brand-name { left: 0; width: 613px; text-align: center; top: 140px; font-size: 84px; color: var(--pink); }
  .card--back-white .brand-block {
    position: absolute; left: 0; width: 613px; top: 120px;
    display: flex; flex-direction: column; align-items: center;
  }
  .card--back-white .brand-name { position: static; color: var(--white); }
  .brand-name--main { font-size: 84px; }
  .brand-name--sub { font-size: 30px; letter-spacing: 2px; margin-top: 6px; }
  .brand-mark { width: 18px; height: 18px; background: var(--pink); margin-bottom: 14px; }
  .divider { position: absolute; left: 237px; top: 59px; width: 3px; height: 236px; background: var(--pink); }
  .contact { position: absolute; left: 298px; top: 108px; color: var(--white); font-family: "Arimo", sans-serif; }
  .contact__name { font: 400 19px/1 "Ultra", serif; color: var(--pink); letter-spacing: 0.2px; }
  .contact__email { font-size: 18px; margin-top: 14px; }
  .contact__phone { font-size: 13.5px; margin-top: 9px; }
  .contact__web { font-size: 18px; margin-top: 36px; }
</style>
</head>
<body>
<main class="sheet">
  <div class="option-label">A1</div>

  <section class="card card--front">
    <div class="backdrop-name" aria-hidden="true">RWT</div>
    <div class="brand-name">RWT</div>
    <div class="divider"></div>
    <div class="contact">
      <p class="contact__name">Marcela Tavares Rocha</p>
      <p class="contact__email">marcela@rwtimoveis-exemplo.com.br</p>
      <p class="contact__phone">0055 418 731 6042</p>
      <p class="contact__web">www.RWTimoveis-exemplo.com.br</p>
    </div>
  </section>

  <section class="card card--back-pink">
    <div class="backdrop-name" aria-hidden="true">RWT</div>
    <div class="brand-name">RWT</div>
  </section>

  <section class="card card--back-white">
    <div class="backdrop-name" aria-hidden="true">RWT</div>
    <div class="brand-block">
      <div class="brand-mark"></div>
      <div class="brand-name brand-name--main">RWT</div>
      <div class="brand-name brand-name--sub">IMOVEIS</div>
    </div>
  </section>
</main>
</body>
</html>
```